Residential Remodeling Contractor needs updated business card

I need a new design for my business card.
Name of the company is Ridgefell Construction. I need a card that commands presence, strength, integrity. I have been in business for 28 years. I am a Residential Remodeling Contractor that covers all aspects of a residential remodel and build.

```html
<!DOCTYPE html>
<html lang="en">
<head>
<meta charset="utf-8">
<title>Ridgefell Construction – Business Card</title>
<link rel="stylesheet" href="https://fonts.googleapis.com/css2?family=Cinzel:wght@600&family=Arimo:wght@400&display=swap">
<style>
  :root {
    --brand-blue: #1a3f7e;
    --accent-blue: #3a5aa8;
    --paper: #ffffff;
    --backdrop: #d9dadc;
  }
  html, body {
    margin: 0;
    padding: 0;
    width: 1200px;
    height: 901px;
    overflow: hidden;
    background: var(--backdrop);
  }
  .sheet {
    position: relative;
    width: 1200px;
    height: 901px;
    display: flex;
    align-items: center;
    justify-content: center;
    gap: 40px;
  }
  .card {
    position: relative;
    width: 540px;
    height: 310px;
    border-radius: 18px;
    overflow: hidden;
    box-shadow: 0 6px 18px rgba(0,0,0,0.18);
  }
  .card-front {
    background: var(--brand-blue);
    display: flex;
    align-items: center;
    justify-content: center;
  }
  .wordmark {
    display: flex;
    align-items: center;
    gap: 14px;
    font-family: "Cinzel", Georgia, serif;
    font-weight: 600;
    line-height: 1.05;
  }
  .wordmark-square {
    width: 18px;
    height: 18px;
    flex: none;
  }
  .wordmark-text span { display: block; }
  .card-front .wordmark { color: var(--paper); font-size: 38px; }
  .card-front .wordmark-square { background: var(--paper); width: 26px; height: 26px; }

  .card-back { background: var(--paper); }
  .card-back .wave { position: absolute; inset: 0; }
  .card-back .wordmark {
    position: absolute;
    top: 34px;
    right: 36px;
    color: var(--brand-blue);
    font-size: 24px;
  }
  .card-back .wordmark-square { background: var(--brand-blue); }

  .contact {
    position: absolute;
    left: 40px;
    top: 196px;
    color: var(--paper);
    font-family: "Arimo", Arial, sans-serif;
    font-size: 12px;
  }
  .contact-name {
    font-family: "Cinzel", Georgia, serif;
    font-weight: 600;
    font-size: 16px;
    letter-spacing: 0.5px;
  }
  .contact-role { margin-bottom: 8px; }
  .contact-list { list-style: none; margin: 0; padding: 0; }
  .contact-list li { display: flex; align-items: center; gap: 8px; height: 16px; }
  .contact-list svg { width: 10px; height: 10px; fill: var(--paper); }

  .address {
    position: absolute;
    right: 32px;
    top: 222px;
    text-align: right;
    color: var(--paper);
    font-family: "Arimo", Arial, sans-serif;
    font-size: 12px;
    line-height: 18px;
  }
</style>
</head>
<body>
<main class="sheet">
  <section class="card card-front" aria-label="Card front">
    <div class="wordmark">
      <div class="wordmark-square"></div>
      <div class="wordmark-text"><span>Ridgefell</span><span>Construction</span></div>
    </div>
  </section>

  <section class="card card-back" aria-label="Card back">
    <svg class="wave" viewBox="0 0 540 310" preserveAspectRatio="none" aria-hidden="true">
      <path d="M0,310 L0,250 C20,200 60,178 150,172 L300,166 C420,160 500,125 540,50 L540,310 Z" fill="var(--brand-blue)"/>
      <path d="M8,238 C40,190 90,168 160,162 L300,156 C410,150 480,120 525,62" fill="none" stroke="var(--accent-blue)" stroke-width="3" opacity="0.7"/>
      <path d="M30,208 C70,178 120,166 190,163" fill="none" stroke="var(--accent-blue)" stroke-width="2" opacity="0.5"/>
    </svg>

    <div class="wordmark">
      <div class="wordmark-square"></div>
      <div class="wordmark-text"><span>Ridgefell</span><span>Construction</span></div>
    </div>

    <div class="contact">
      <div class="contact-name">DANIEL WHITCOMBE</div>
      <div class="contact-role">Owner &amp; Manager</div>
      <ul class="contact-list">
        <li><svg viewBox="0 0 10 10"><path d="M1,3 Q5,0 9,3 L8,4 L6,3 L4,3 L2,4 Z M2,5 H8 V9 H2 Z"/></svg>555 201 4478</li>
        <li><svg viewBox="0 0 10 10"><rect x="2.5" y="0.5" width="5" height="9" rx="1" fill="none" stroke="#fff"/></svg>555-310-72864</li>
        <li><svg viewBox="0 0 10 10"><path d="M0.5,2 H9.5 V8 H0.5 Z M0.5,2 L5,5.5 L9.5,2" fill="none" stroke="#fff"/></svg>info@ridgefellbuild.com</li>
        <li><svg viewBox="0 0 10 10"><circle cx="5" cy="5" r="4.5"/></svg>www.ridgefellbuild.com</li>
      </ul>
    </div>

    <div class="address">
      P.O. Box&nbsp; Street Name<br>
      Country Name AB, A5B 521
    </div>
  </section>
</main>
</body>
</html>
```